A start-up named "Corvane Therapeutics" - needs a new PowerPoint design

We need a new PowerPoint Design for an early-stage start-up named "Corvane Therapeutics" seeking to disrupt the current approach towards drug discovery within aging disorders.

We would like to build on Corvane's legacy, the founder of the modern science of genetics, by employing a multidisciplinary approach, experimenting, and providing elderly patients the attention they deserve.

We have selected the suffix "therapeutics" intentionally as it stands for (a medicine) the treatment of disease; the science of healing. Alzheimer’s treatment is a huge, urgent, unmet need:
- Shift from a disease-management system to a preventive medicine system
- Focus on increasing the health span, not only the life span

Target Market(s)

Pharma/ Biotech Executives Medical Institutions Healthcare professionals (MDs, nurses, payors, pharmacists, etc.) Patients

Industry/Entity Type

Healthcare

Other font styles liked:
• Celias

Colors
0054AA
0677BA
7BADD7
CADEEF
E8F1F8
E54698
E96AAD
F1A4CE
F9D9EA
FCEFF6
A7469A
B969AE
D3A5CF
EDDBEB
F8F0F9
6B429C
8869AF
B7A5CE
E3DAEB
F3F0F8

Requirements
Must have
• - differentiate from other companies named after Corvane - differentiate from other Pharma/ Biotech companies
Nice to have
• simplicity/ minimalist logo vivid colors gradient 3D Life-Sciences inspired Simple geometry Balance
Should not have
• mascot/ emblem watermark logo animated ink style nature-inspired inventive typography artistic chaos

```html
<!DOCTYPE html>
<html lang="en">
<head>
<meta charset="utf-8">
<title>Corvane Therapeutics – Presentation Template</title>
<link href="https://fonts.googleapis.com/css2?family=Lato:wght@300;400;700;900&display=swap" rel="stylesheet">
<style>
:root{
  --page:#ffffff;
  --violet-deep:#7d0a96;
  --violet-mid:#a50fc0;
  --magenta-glow:#d914ef;
  --orange:#eba122;
  --white:#ffffff;
  --ink-magenta:#b0139f;
  --tl-1:#eea322;
  --tl-2:#3fc4ee;
  --tl-3:#28287f;
  --tl-4:#ff8a12;
  --tl-5:#ee1f3b;
}
*{margin:0;padding:0;box-sizing:border-box}
html,body{width:847px;height:1200px;overflow:hidden;background:var(--page)}
body{position:relative;font-family:"Lato",sans-serif;color:var(--white)}
.slide{position:absolute;width:363px;height:256px;overflow:hidden;
  background:radial-gradient(ellipse 70% 70% at 50% 50%,var(--magenta-glow) 0%,var(--violet-mid) 55%,var(--violet-deep) 100%);
  box-shadow:0 4px 6px rgba(0,0,0,.25)}
.col-a{left:52px}.col-b{left:434px}
.row-1{top:59px}.row-2{top:330px}.row-3{top:598px}.row-4{top:868px}
.abs{position:absolute}
.slide-title{position:absolute;left:0;right:0;text-align:center;top:34px;font-weight:400;font-size:18px;letter-spacing:.2px}
.brand{position:absolute;font-weight:400;color:var(--white);line-height:1}
.brand .name{display:block}
.brand .sub{display:block;letter-spacing:.14em}
.brand-footer{left:21px;top:228px}
.brand-footer .name{font-size:11px}
.brand-footer .sub{font-size:5px;margin-top:1px}
.page-num{position:absolute;right:0;bottom:0;width:27px;height:27px}
.page-num span{position:absolute;right:7px;bottom:7px;font-size:7px;color:var(--ink-magenta)}
/* cover */
.cover-brand{left:76px;top:46px}
.cover-brand .name{font-size:40px;font-weight:400}
.cover-brand .sub{font-size:15px;margin-top:4px}
.cover-title{left:76px;top:145px;font-weight:300;font-size:21px;line-height:1.25}
/* agenda */
.agenda-item{position:absolute;width:154px;height:34px}
.agenda-pill{position:absolute;left:14px;top:0;right:0;bottom:0;border-radius:0 17px 17px 0;
  background:linear-gradient(var(--white) 0 35%,var(--orange) 35% 100%);border-radius:17px}
.agenda-head{position:absolute;left:45px;top:5px;font-size:5px;font-weight:700;color:var(--ink-magenta)}
.agenda-text{position:absolute;left:45px;top:15px;width:104px;font-size:4.3px;line-height:1.5;color:var(--ink-magenta)}
.icon-disc{position:absolute;left:0;top:-2px;width:38px;height:38px;border-radius:50%;background:var(--white);border:3px solid #9a2a8e}
.icon-disc svg{position:absolute;left:7px;top:7px;width:18px;height:18px}
/* section */
.section-mark{left:60px;top:74px;width:62px;height:62px;border:3px solid var(--white);border-radius:50%;
  font-size:17px;font-weight:700;display:flex;align-items:center;justify-content:center}
.section-title{left:135px;top:90px;font-weight:900;font-size:18px;letter-spacing:.3px}
.section-sub{left:135px;top:113px;font-weight:400;font-size:17px}
/* services */
.service-card{position:absolute;width:77px;height:68px;border-radius:4px;overflow:hidden;
  background:linear-gradient(var(--white) 0 46%,var(--orange) 46% 100%)}
.service-card .icon-ring{position:absolute;left:21px;top:10px;width:35px;height:35px;border-radius:50%;background:var(--white);border:1.5px solid var(--ink-magenta)}
.service-card .icon-ring svg{position:absolute;left:7px;top:7px;width:18px;height:18px}
.service-card .label{position:absolute;left:0;right:0;bottom:9px;text-align:center;font-size:7px;font-weight:700;color:var(--white)}
/* timeline */
.tl-note{position:absolute;width:62px;font-size:4.8px;line-height:1.5;font-weight:700}
/* portfolio */
.portfolio-photo{left:14px;top:72px;width:160px;height:124px;
  background:linear-gradient(135deg,#e8e0d4 0%,#c9b49c 45%,#8f7a70 100%)}
.portfolio-copy{left:188px;top:70px;width:158px;font-size:4.8px;line-height:1.45;font-weight:700;text-align:justify}
.portfolio-copy p{margin-bottom:6px}
/* team */
.member{position:absolute;width:90px;text-align:center}
.member .portrait{width:60px;height:60px;border-radius:50%;margin:0 auto;background:var(--white);border:3px solid #9a2a8e}
.member .who{margin-top:10px;font-size:5px;font-weight:700}
.member .bio{margin-top:4px;font-size:4.8px;line-height:1.5;font-weight:700}
/* contact */
.contact-brand{left:21px;top:118px}
.contact-brand .name{font-size:27px}
.contact-brand .sub{font-size:11px;margin-top:3px}
.contact-rule{left:188px;top:113px;width:1.5px;height:48px;background:var(--white)}
.contact-list{left:196px;top:114px;list-style:none}
.contact-list li{display:flex;align-items:center;height:12px;font-size:6.4px;font-weight:700}
.contact-list svg{width:8px;height:8px;margin-right:9px}
</style>
</head>
<body>

<!-- 1 Cover -->
<section class="slide col-a row-1">
  <div class="brand cover-brand"><span class="name">Corvane</span><span class="sub">Therapeutics</span></div>
  <h1 class="abs cover-title">HERE GOES YOUR<br>PRESENTATION TITLE.</h1>
</section>

<!-- 2 Agenda -->
<section class="slide col-b row-1">
  <h2 class="slide-title">OUR AGENDA</h2>
  <div class="agenda-item" style="left:14px;top:78px">
    <div class="agenda-pill"></div>
    <div class="icon-disc"><svg viewBox="0 0 24 24" fill="none" stroke="#b0139f" stroke-width="1.5"><rect x="5" y="4" width="14" height="17" rx="1"/><path d="M9 9l1.5 1.5L13 8M9 14l1.5 1.5L13 13M15 9h2M15 14h2"/></svg></div>
    <div class="agenda-head">HEADING1</div>
    <div class="agenda-text">Lorem ipsum dolor sit amet, consectetur adipiscing elit. Aenean eget dolor erat.</div>
  </div>
  <div class="agenda-item" style="left:191px;top:78px">
    <div class="agenda-pill"></div>
    <div class="icon-disc"><svg viewBox="0 0 24 24" fill="none" stroke="#b0139f" stroke-width="1.5"><path d="M12 3c3 4 5 6 5 9a5 5 0 0 1-10 0c0-3 2-5 5-9z"/><path d="M12 10v5M9.5 12.5h5"/></svg></div>
    <div class="agenda-head">HEADING2</div>
    <div class="agenda-text">Lorem ipsum dolor sit amet, consectetur adipiscing elit. Aenean eget dolor erat.</div>
  </div>
  <div class="agenda-item" style="left:14px;top:146px">
    <div class="agenda-pill"></div>
    <div class="icon-disc"><svg viewBox="0 0 24 24" fill="none" stroke="#b0139f" stroke-width="1.5"><circle cx="6" cy="6" r="2.5"/><circle cx="18" cy="6" r="2.5"/><circle cx="6" cy="18" r="2.5"/><circle cx="18" cy="18" r="2.5"/><circle cx="12" cy="12" r="2.5"/></svg></div>
    <div class="agenda-head">HEADING3</div>
    <div class="agenda-text">Lorem ipsum dolor sit amet, consectetur adipiscing elit. Aenean eget dolor erat.</div>
  </div>
  <div class="agenda-item" style="left:191px;top:146px">
    <div class="agenda-pill"></div>
    <div class="icon-disc"><svg viewBox="0 0 24 24" fill="none" stroke="#b0139f" stroke-width="1.5"><path d="M12 20s-8-5-8-11a4 4 0 0 1 8-1 4 4 0 0 1 8 1c0 6-8 11-8 11z"/><path d="M5 12h4l1.5-3 2 5 1.5-2h5"/></svg></div>
    <div class="agenda-head">HEADING4</div>
    <div class="agenda-text">Lorem ipsum dolor sit amet, consectetur adipiscing elit. Aenean eget dolor erat.</div>
  </div>
  <div class="brand brand-footer"><span class="name">Corvane</span><span class="sub">Therapeutics</span></div>
  <div class="page-num"><svg width="27" height="27"><polygon points="27,0 27,27 0,27" fill="#fff"/></svg><span>2</span></div>
</section>

<!-- 3 Section -->
<section class="slide col-a row-2">
  <div class="abs section-mark">01</div>
  <h2 class="abs section-title">SECTION TITLE</h2>
  <p class="abs section-sub">Here Goes Subtitle</p>
</section>

<!-- 4 Services -->
<section class="slide col-b row-2">
  <h2 class="slide-title" style="top:35px">OUR SERVICES</h2>
  <div class="service-card" style="left:35px;top:65px"><div class="icon-ring"><svg viewBox="0 0 24 24" fill="none" stroke="#b0139f" stroke-width="1.5"><path d="M6 4c-2 2-2 5 1 9s6 7 9 7l2-3-3-2-2 1c-2-1-4-3-5-5l1-2-2-3z"/></svg></div><div class="label">SERVICE1</div></div>
  <div class="service-card" style="left:140px;top:65px"><div class="icon-ring"><svg viewBox="0 0 24 24" fill="none" stroke="#b0139f" stroke-width="1.5"><circle cx="12" cy="12" r="3"/><circle cx="12" cy="12" r="7" stroke-dasharray="3 2"/></svg></div><div class="label">SERVICE2</div></div>
  <div class="service-card" style="left:244px;top:65px"><div class="icon-ring"><svg viewBox="0 0 24 24" fill="none" stroke="#b0139f" stroke-width="1.5"><path d="M6 3v6a4 4 0 0 0 8 0V3M10 13v3a4 4 0 0 0 8 0v-2"/><circle cx="18" cy="12" r="2"/></svg></div><div class="label">SERVICE3</div></div>
  <div class="service-card" style="left:35px;top:151px"><div class="icon-ring"><svg viewBox="0 0 24 24" fill="none" stroke="#b0139f" stroke-width="1.5"><circle cx="12" cy="12" r="8"/><text x="12" y="14.5" font-size="6.5" text-anchor="middle" fill="#b0139f" stroke="none" font-family="Lato,sans-serif">24/7</text></svg></div><div class="label">SERVICE4</div></div>
  <div class="service-card" style="left:140px;top:151px"><div class="icon-ring"><svg viewBox="0 0 24 24" fill="none" stroke="#b0139f" stroke-width="1.5"><path d="M7 12V6m3 5V4m3 7V4m3 8V6M7 12c0 5 2 8 5 8s5-3 5-6l2-3"/></svg></div><div class="label">SERVICE5</div></div>
  <div class="service-card" style="left:244px;top:151px"><div class="icon-ring"><svg viewBox="0 0 24 24" fill="none" stroke="#b0139f" stroke-width="1.5"><rect x="5" y="4" width="14" height="16" rx="1"/><path d="M12 10v6M9 13h6"/></svg></div><div class="label">SERVICE6</div></div>
  <div class="brand brand-footer"><span class="name">Corvane</span><span class="sub">Therapeutics</span></div>
  <div class="page-num"><svg width="27" height="27"><polygon points="27,0 27,27 0,27" fill="#fff"/></svg><span>4</span></div>
</section>

<!-- 5 Timeline -->
<section class="slide col-a row-3">
  <h2 class="slide-title">TIMELINE</h2>
  <svg class="abs" style="left:0;top:0" width="363" height="256" viewBox="0 0 363 256">
    <g stroke-width="1.2">
      <line x1="85" y1="88" x2="85" y2="136" stroke="#3fc4ee"/>
      <line x1="217" y1="88" x2="217" y2="136" stroke="#ff8a12"/>
      <line x1="19" y1="151" x2="19" y2="194" stroke="#eea322"/>
      <line x1="150" y1="151" x2="150" y2="194" stroke="#28287f"/>
      <line x1="283" y1="151" x2="283" y2="194" stroke="#ee1f3b"/>
    </g>
    <polygon points="19,136 82,136 89,143.5 82,151 19,151" fill="#eea322"/>
    <polygon points="85,136 148,136 155,143.5 148,151 85,151 92,143.5" fill="#3fc4ee"/>
    <polygon points="151,136 214,136 221,143.5 214,151 151,151 158,143.5" fill="#28287f"/>
    <polygon points="217,136 280,136 287,143.5 280,151 217,151 224,143.5" fill="#ff8a12"/>
    <polygon points="283,136 343,136 350,143.5 343,151 283,151 290,143.5" fill="#ee1f3b"/>
    <g font-family="Lato,sans-serif" font-weight="700" font-size="6.5" fill="#fff" text-anchor="middle">
      <text x="48" y="146">YEAR 1</text><text x="116" y="146">YEAR 2</text><text x="182" y="146">YEAR 3</text><text x="248" y="146">YEAR 4</text><text x="316" y="146">YEAR 5</text>
    </g>
    <g fill="#fff" stroke-width="1.3">
      <circle cx="85" cy="80" r="8" stroke="#3fc4ee"/>
      <circle cx="217" cy="80" r="8" stroke="#ff8a12"/>
      <circle cx="19" cy="202" r="8" stroke="#eea322"/>
      <circle cx="150" cy="202" r="8" stroke="#28287f"/>
      <circle cx="283" cy="202" r="8" stroke="#ee1f3b"/>
    </g>
  </svg>
  <p class="tl-note" style="left:88px;top:100px">Lorem ipsum dolor sit amet, consectetur adipiscing elit. Aenean eget dolor erat.</p>
  <p class="tl-note" style="left:220px;top:100px">Lorem ipsum dolor sit amet, consectetur adipiscing elit. Aenean eget dolor erat.</p>
  <p class="tl-note" style="left:24px;top:162px">Lorem ipsum dolor sit amet, consectetur adipiscing elit. Aenean eget dolor erat.</p>
  <p class="tl-note" style="left:154px;top:162px">Lorem ipsum dolor sit amet, consectetur adipiscing elit. Aenean eget dolor erat.</p>
  <p class="tl-note" style="left:288px;top:162px">Lorem ipsum dolor sit amet, consectetur adipiscing elit. Aenean eget dolor erat.</p>
  <div class="brand brand-footer"><span class="name">Corvane</span><span class="sub">Therapeutics</span></div>
  <div class="page-num"><svg width="27" height="27"><polygon points="27,0 27,27 0,27" fill="#fff"/></svg><span>5</span></div>
</section>

<!-- 6 Portfolio -->
<section class="slide col-b row-3">
  <h2 class="slide-title">PORTFOLIO PRESENTATION</h2>
  <div class="abs portfolio-photo" role="img" aria-label="Photo collage of caregivers spending time with elderly patients"></div>
  <div class="abs portfolio-copy">
    <p>Lorem ipsum dolor sit amet, consectetur adipiscing elit. Aenean eget dolor erat. Fusce erat purus, dapibus volutpat ligula vel, rutrum faucibus lacus. Morbi malesuada .</p>
    <p>Lorem ipsum dolor sit amet, consectetur adipiscing elit. Aenean eget dolor erat. Fusce erat purus, dapibus volutpat ligula vel, rutrum faucibus lacus. Morbi malesuada .</p>
    <p>Lorem ipsum dolor sit amet, consectetur adipiscing elit. Aenean eget dolor erat. Fusce erat purus, dapibus volutpat ligula vel, rutrum faucibus lacus. Morbi malesuada .</p>
  </div>
  <div class="brand brand-footer"><span class="name">Corvane</span><span class="sub">Therapeutics</span></div>
  <div class="page-num"><svg width="27" height="27"><polygon points="27,0 27,27 0,27" fill="#fff"/></svg><span>6</span></div>
</section>

<!-- 7 Team -->
<section class="slide col-a row-4">
  <h2 class="slide-title">OUR TEAM</h2>
  <div class="member" style="left:10px;top:86px"><div class="portrait" role="img" aria-label="Team member portrait placeholder"></div><p class="who">JOHN DOE</p><p class="bio">Lorem ipsum dolor sit amet, consectetur adipiscing elit. Aenean eget dolor erat.</p></div>
  <div class="member" style="left:136px;top:86px"><div class="portrait" role="img" aria-label="Team member portrait placeholder"></div><p class="who">JANE DOE</p><p class="bio">Lorem ipsum dolor sit amet, consectetur adipiscing elit. Aenean eget dolor erat.</p></div>
  <div class="member" style="left:261px;top:86px"><div class="portrait" role="img" aria-label="Team member portrait placeholder"></div><p class="who">JOHN DOE 2</p><p class="bio">Lorem ipsum dolor sit amet, consectetur adipiscing elit. Aenean eget dolor erat.</p></div>
  <div class="brand brand-footer"><span class="name">Corvane</span><span class="sub">Therapeutics</span></div>
  <div class="page-num"><svg width="27" height="27"><polygon points="27,0 27,27 0,27" fill="#fff"/></svg><span>7</span></div>
</section>

<!-- 8 Contact -->
<section class="slide col-b row-4">
  <h2 class="slide-title">CONTACT US</h2>
  <div class="brand contact-brand"><span class="name">Corvane</span><span class="sub">Therapeutics</span></div>
  <div class="abs contact-rule"></div>
  <ul class="abs contact-list">
    <li><svg viewBox="0 0 16 16"><circle cx="8" cy="8" r="8" fill="#fff"/><path d="M8 4a2.5 2.5 0 0 1 2.5 2.5C10.5 9 8 12 8 12S5.5 9 5.5 6.5A2.5 2.5 0 0 1 8 4z" fill="#a50fc0"/></svg>Lorem ipsum dolor sit amet, consectetur</li>
    <li><svg viewBox="0 0 16 16"><circle cx="8" cy="8" r="8" fill="#fff"/><path d="M5.5 4.5c-1 1 0 3.5 1.8 5.2s4.2 2.8 5.2 1.8l-1.6-1.6-1.2.7C8.8 10 7 8.2 6.4 7.3l.7-1.2z" fill="#a50fc0"/></svg>555-014-2290</li>
    <li><svg viewBox="0 0 16 16"><circle cx="8" cy="8" r="8" fill="#fff"/><rect x="4.5" y="5.5" width="7" height="5" fill="none" stroke="#a50fc0"/><path d="M4.5 5.5L8 8.5l3.5-3" fill="none" stroke="#a50fc0"/></svg>www.corvanetx.com</li>
    <li><svg viewBox="0 0 16 16"><circle cx="8" cy="8" r="8" fill="#fff"/><circle cx="8" cy="8" r="3.8" fill="none" stroke="#a50fc0"/><path d="M4.2 8h7.6M8 4.2c-1.6 2.4-1.6 5.2 0 7.6M8 4.2c1.6 2.4 1.6 5.2 0 7.6" fill="none" stroke="#a50fc0" stroke-width=".7"/></svg>hello@corvanetx.com</li>
  </ul>
  <div class="page-num"><svg width="27" height="27"><polygon points="27,0 27,27 0,27" fill="#fff"/></svg><span>8</span></div>
</section>

</body>
</html>
```